Stylish High End Wedding Videography/Films Website (BMRT)

We need a modern and high-end website look for our wedding video and films business. We films weddings all over the United Kingdom and at European destinations so need something to reflect our work. The website should be visually stunning with images and videos being the focal point as this is what our services are;

I have uploads of some items I like and the features the site needs to have. These have been taken from other websites using standout features.

We need the following pages;

1 - Homepage
2 - Films Index Page
3 - Individual Films Page
4 - Prices / Collection Page
5 - Reviews
6 - Options
7 - About
8 - Contact
9 - Blog Index
10 - Blog Page

All pages must be consistent so have a similar style.

Pages on menu:
Films
Prices
Reviews
Options
About
Contact

We require a responsive look too. Over 90% of our visitors access the website via their mobile devices.

Please use the colours from our logo to incorporate into the website.

Target Market(s)

Wedding Couples

Industry/Entity Type

Wedding Photography

Number of Pages Required

5+ page

Font styles to use
Sans Serif
Script

Requirements
Must have
• The logo must be in the centre of the menu at the top.

Social icons at the bottom of the page.

Use only two fonts including Lore which is supplied
Nice to have
• Different video for each page on the top header. This will play behind the menu.

```html
<!DOCTYPE html>
<html lang="en">
<head>
<meta charset="utf-8">
<title>BMRT Wedding Films</title>
<link rel="stylesheet" href="https://fonts.googleapis.com/css2?family=Jost:wght@400;500;600;700&family=Josefin+Sans:wght@400;600&display=swap">
<style>
:root{
  --gold:#a68f55;
  --gold-dark:#8f7a45;
  --ink:#111;
  --black:#000;
  --white:#fff;
  --ghost:#efebe2;
  --section-grey:#f6f6f6;
  --panel-grey:#ebebeb;
}
*{margin:0;padding:0;box-sizing:border-box}
html,body{width:1200px;height:4950px;overflow:hidden}
body{position:relative;background:var(--white);font-family:"Jost",sans-serif;color:var(--ink)}
.abs{position:absolute}

/* top bar */
.topbar{left:0;top:0;width:1200px;height:30px;background:var(--black);color:var(--white);font-size:12px;letter-spacing:.5px}
.topbar .welcome{left:88px;top:8px}
.topbar .phone{right:88px;top:8px;display:flex;align-items:center;gap:10px}

/* header */
.brand{left:0;width:1200px;top:44px;text-align:center;color:var(--gold-dark);font-weight:500}
.brand .mark{display:block;width:26px;height:26px;margin:0 auto 8px;border:2px solid var(--gold-dark)}
.brand .name{display:block;font-size:15px;letter-spacing:5px;line-height:1}
.brand .tag{display:block;font-size:8px;letter-spacing:4px;margin-top:3px}
.nav{left:0;width:1200px;top:128px;display:flex;justify-content:center;gap:38px;font-size:13px;letter-spacing:.5px}
.nav a{color:var(--ink);text-decoration:none}
.nav a.active{color:var(--gold)}

/* hero */
.hero-photo{left:0;top:160px;width:1200px;height:686px;background:
  radial-gradient(ellipse 180px 150px at 58% 72%,#5b3fa0 0%,rgba(91,63,160,.55) 55%,rgba(91,63,160,0) 100%),
  radial-gradient(ellipse 260px 300px at 48% 38%,#c9a08a 0%,rgba(160,120,100,.6) 45%,rgba(60,55,60,0) 100%),
  linear-gradient(100deg,#1c2230 0%,#3a4150 30%,#4d4a4c 55%,#2a2c33 80%,#141519 100%)}
.hero-band{left:0;top:760px;width:1200px;height:90px}
.hero-caption{left:0;width:1200px;top:778px;text-align:center;color:var(--white);font-weight:600;font-size:20px;letter-spacing:.4px}
.play{width:88px;height:88px}

/* section headings */
.ornament-area{width:180px;height:172px;left:510px;background:radial-gradient(ellipse 50% 50% at 50% 50%,rgba(60,55,45,.16) 0%,rgba(60,55,45,.07) 55%,rgba(60,55,45,0) 100%)}
.section-title{width:1200px;left:0;text-align:center;font-family:"Josefin Sans",sans-serif;color:var(--gold);font-size:36px;font-weight:600;letter-spacing:.5px;line-height:40px}
.ghost{font-weight:700;color:var(--ghost);font-size:86px;letter-spacing:2px;line-height:1;white-space:nowrap}

.body-copy{font-size:12.5px;line-height:23px;text-transform:uppercase;letter-spacing:.2px}
.body-copy p+p{margin-top:23px}
.btn{background:var(--gold);color:var(--white);font-size:13px;font-weight:600;letter-spacing:.6px;display:flex;align-items:center;justify-content:center;border-radius:3px}

/* gallery */
.gallery{left:65px;top:1806px;width:1070px;height:556px;display:grid;grid-template-columns:repeat(3,1fr);grid-template-rows:repeat(2,1fr)}
.gallery div{position:relative}

/* options */
.options-bg{left:0;top:2538px;width:1200px;height:1177px;background:var(--section-grey)}
.option-panel{background:var(--panel-grey);padding:0 34px}
.option-panel h3{font-family:"Josefin Sans",sans-serif;color:var(--gold);font-size:27px;font-weight:600;letter-spacing:.3px;margin-bottom:30px}
.option-panel .body-copy{font-size:12.5px}

/* reviews */
.arrow-btn{width:46px;height:46px;border:1px solid #cfcfcf;display:flex;align-items:center;justify-content:center}
.review-name{left:0;width:1200px;text-align:center;font-size:20px;color:var(--gold);letter-spacing:.5px}
.review-place{left:0;width:1200px;text-align:center;font-size:16px;font-weight:500;letter-spacing:.5px}

/* footer */
.footer{left:0;top:4550px;width:1200px;height:400px;background:var(--gold)}
.footer .brand-foot{left:140px;top:30px;width:270px;text-align:center;color:var(--white);font-weight:500}
.foot-col{color:var(--white);font-size:14px;letter-spacing:.4px}
.foot-col h4{font-size:15px;font-weight:600;margin-bottom:18px}
.foot-col li{list-style:none;height:38px}
.badge{left:902px;top:4722px;width:124px;height:124px;border-radius:50%;background:#f6efb8;border:2px solid #222}
.foot-rule{left:86px;top:4906px;width:1048px;height:1px;background:rgba(255,255,255,.7)}
.legal{left:110px;top:4920px;color:var(--white);font-size:15px;font-weight:600;letter-spacing:.5px}
.social{top:4919px;width:22px;height:22px;border:2px solid var(--white);border-radius:3px}
</style>
</head>
<body>

<!-- top bar -->
<div class="abs topbar">
  <span class="abs welcome">WELCOME TO OUR WEBSITE</span>
  <span class="abs phone">
    <svg width="13" height="13" viewBox="0 0 24 24" aria-hidden="true"><path fill="#fff" d="M6.6 10.8a15.1 15.1 0 0 0 6.6 6.6l2.2-2.2a1 1 0 0 1 1-.25 11.4 11.4 0 0 0 3.6.57 1 1 0 0 1 1 1V20a1 1 0 0 1-1 1A17 17 0 0 1 3 4a1 1 0 0 1 1-1h3.5a1 1 0 0 1 1 1c0 1.25.2 2.45.57 3.57a1 1 0 0 1-.25 1z"/></svg>
    07700 900 123
  </span>
</div>

<!-- header -->
<div class="abs brand">
  <span class="mark"></span>
  <span class="name">BMRT</span>
  <span class="tag">WEDDING FILMS</span>
</div>
<nav class="abs nav">
  <a class="active" href="#">HOME</a><a href="#">FILMS</a><a href="#">PRICES</a><a href="#">REVIEWS</a><a href="#">OPTIONS</a><a href="#">ABOUT</a><a href="#">CONTACT</a>
</nav>

<!-- hero -->
<div class="abs hero-photo" role="img" aria-label="Bride holding a purple and white bouquet stepping out of a wedding car"></div>
<svg class="abs play" style="left:556px;top:417px" viewBox="0 0 88 88" aria-hidden="true">
  <circle cx="44" cy="44" r="43" fill="rgba(255,255,255,.35)"/>
  <path d="M34 26 L64 44 L34 62 Z" fill="#fff"/>
</svg>
<svg class="abs hero-band" viewBox="0 0 1200 90" preserveAspectRatio="none" aria-hidden="true">
  <path d="M0 0 H1200 V86 Q600 40 0 86 Z" fill="#000"/>
</svg>
<div class="abs hero-caption">WEDDING VIDEOGRAPHY - NORTH EAST, UK AND WORLDWIDE FILMS</div>

<!-- about -->
<div class="abs ornament-area" style="top:935px" role="img" aria-label="Black scroll ornament framing the heading"></div>
<div class="abs ghost" style="left:68px;top:1050px">WE ARE</div>
<div class="abs section-title" style="top:999px">ABOUT US</div>

<div class="abs body-copy" style="left:65px;top:1152px;width:535px">
  <p>I'm a filmmaker who loves documenting couples' most important day of their lives. Based in County Durham I film weddings mostly in the North East of England however regularly travel around the UK and Europe.</p>
  <p>I first picked up a video camera when I was 8 years old making home movies documenting family holidays and events and it led me onto gaining a degree in TV and Radio production at university.</p>
</div>
<div class="abs btn" style="left:65px;top:1392px;width:135px;height:46px">READ MORE</div>

<svg class="abs" style="left:713px;top:1138px" width="358" height="323" viewBox="0 0 358 323" role="img" aria-label="Film frame with a bride and groom embracing in autumn woods">
  <defs>
    <pattern id="holes-a" x="14" y="0" width="32" height="26" patternUnits="userSpaceOnUse"><rect x="0" y="0" width="18" height="24" rx="3" fill="#fff"/></pattern>
    <radialGradient id="photo-a" cx="50%" cy="55%" r="70%">
      <stop offset="0" stop-color="#d9b48e"/><stop offset=".35" stop-color="#8a5a3e"/><stop offset=".7" stop-color="#9b8a3c"/><stop offset="1" stop-color="#5e5a26"/>
    </radialGradient>
  </defs>
  <rect width="358" height="323" fill="#000"/>
  <rect x="0" y="14" width="358" height="26" fill="url(#holes-a)"/>
  <rect x="0" y="281" width="358" height="26" fill="url(#holes-a)"/>
  <rect x="8" y="48" width="342" height="226" fill="url(#photo-a)"/>
  <text x="12" y="318" fill="#e0c040" font-size="11" font-family="Jost,sans-serif">21</text>
  <text x="140" y="318" fill="#e0c040" font-size="11" font-family="Jost,sans-serif">21A</text>
</svg>

<!-- galleries -->
<div class="abs ornament-area" style="top:1550px" role="img" aria-label="Black scroll ornament framing the heading"></div>
<div class="abs section-title" style="top:1616px">GALLERIES</div>
<div class="abs ghost" style="left:65px;top:1730px">RECENT WORK</div>

<div class="abs gallery">
  <div role="img" aria-label="Smiling couple close-up" style="background:radial-gradient(ellipse 30% 40% at 30% 55%,#e6c7b2,rgba(230,199,178,0)),radial-gradient(ellipse 30% 45% at 72% 55%,#d9b095,rgba(217,176,149,0)),linear-gradient(180deg,#2a2224,#6b5550 60%,#efe9e4)"></div>
  <div role="img" aria-label="Couple about to kiss, film still" style="background:radial-gradient(ellipse 45% 55% at 55% 45%,#d8c39a,rgba(216,195,154,0)),linear-gradient(135deg,#7d6c48,#b8a271 55%,#5e5236)">
    <svg class="abs" style="left:146px;top:107px" width="64" height="64" viewBox="0 0 88 88" aria-hidden="true"><circle cx="44" cy="44" r="43" fill="rgba(255,255,255,.35)"/><path d="M34 26 L64 44 L34 62 Z" fill="#fff"/></svg>
  </div>
  <div role="img" aria-label="Couple sitting by a mountain river" style="background:radial-gradient(ellipse 22% 30% at 28% 58%,#f2f0ec,rgba(242,240,236,0)),linear-gradient(180deg,#dfe6e8 0%,#4f6a3e 28%,#36502e 60%,#9aa0a0 78%,#6c6a60 100%)"></div>
  <div role="img" aria-label="Couple on a veranda with flowers" style="background:radial-gradient(ellipse 28% 40% at 55% 55%,#efe6de,rgba(239,230,222,0)),radial-gradient(ellipse 40% 12% at 50% 92%,#c43a3a,rgba(196,58,58,0)),linear-gradient(180deg,#d9d9d4,#8c8e7e 60%,#4a4d3c)"></div>
  <div role="img" aria-label="Bride and groom forehead to forehead" style="background:radial-gradient(ellipse 30% 35% at 40% 40%,#e2c8b0,rgba(226,200,176,0)),radial-gradient(ellipse 30% 45% at 75% 65%,#f4efe8,rgba(244,239,232,0)),linear-gradient(135deg,#e0dbd2,#6a7080 60%,#2e3442)"></div>
  <div role="img" aria-label="Bride and groom on a forest hillside" style="background:radial-gradient(ellipse 22% 45% at 55% 75%,#e9d0cc,rgba(233,208,204,0)),linear-gradient(180deg,#8c9a80 0%,#506245 35%,#2f4230 70%,#3d4a38 100%)"></div>
</div>
<div class="abs btn" style="left:538px;top:2405px;width:124px;height:43px">VIEW ALL</div>

<!-- options -->
<div class="abs options-bg"></div>
<div class="abs ornament-area" style="top:2558px" role="img" aria-label="Black scroll ornament framing the heading"></div>
<div class="abs section-title" style="top:2624px">OPTIONS</div>
<div class="abs ghost" style="left:82px;top:2700px;color:#e9e5dc">WEDDING</div>

<div class="abs" style="left:65px;top:2773px;width:558px;height:388px;background:radial-gradient(ellipse 22% 30% at 40% 18%,#d4a6a0,rgba(212,166,160,0)),radial-gradient(ellipse 30% 40% at 62% 50%,#e0b898,rgba(224,184,152,0)),radial-gradient(ellipse 25% 45% at 30% 55%,#8a6244,rgba(138,98,68,0)),linear-gradient(135deg,#2a2e26,#4a4a3a 50%,#1e211c)" role="img" aria-label="Groom kissing bride's forehead, bride with flower crown"></div>
<div class="abs option-panel" style="left:623px;top:2773px;width:512px;height:388px;border-right:4px solid var(--gold);padding-top:72px">
  <h3>CINEMATIC HIGHLIGHTS FILM</h3>
  <div class="body-copy">
    <p>A highlights film, a harmony of moving imagery, vocals and music, which is unique to you.</p>
    <p>I concentrate on the emotion of the day and the people who are important to you.</p>
    <p>This cinematic highlights film is a memory that you will watch for the rest of your lives. This film will outlive lives and generations.</p>
  </div>
</div>

<div class="abs option-panel" style="left:65px;top:3184px;width:512px;height:389px;border-left:4px solid var(--gold);padding:68px 70px 0 42px">
  <h3>CEREMONY AND SPEECHES</h3>
  <div class="body-copy">
    <p>Want to hear the moment you say your vows or I do or even see your first kiss? We film the ceremony in its entirety.</p>
    <p>We also film the entire speeches and toasts so you can relive all those sincere and fun moments.</p>
    <p>We provide you with a separate edit with multiple camera angles.</p>
  </div>
</div>
<div class="abs" style="left:577px;top:3184px;width:558px;height:389px;background:radial-gradient(ellipse 35% 30% at 52% 55%,#e9cbb8,rgba(233,203,184,0)),radial-gradient(ellipse 30% 40% at 25% 30%,#f4ece2,rgba(244,236,226,0)),radial-gradient(ellipse 40% 50% at 25% 75%,#cfc8c2,rgba(207,200,194,0)),linear-gradient(90deg,#b8a898 0%,#8a7a6c 45%,#3a3330 75%,#141212 100%)" role="img" aria-label="Hands exchanging wedding rings"></div>
<div class="abs btn" style="left:536px;top:3621px;width:128px;height:44px">VIEW ALL</div>

<!-- reviews -->
<div class="abs ornament-area" style="top:3806px" role="img" aria-label="Black scroll ornament framing the heading"></div>
<div class="abs section-title" style="top:3872px">REVIEWS</div>
<div class="abs ghost" style="left:65px;top:3970px">CLIENTS SAY'S</div>

<svg class="abs" style="left:77px;top:4052px" width="1048" height="242" viewBox="0 0 1048 242" role="img" aria-label="Film strip of four wedding couple portraits">
  <defs>
    <pattern id="holes-b" x="6" y="0" width="26" height="22" patternUnits="userSpaceOnUse"><rect x="0" y="0" width="15" height="20" rx="3" fill="#fff"/></pattern>
    <radialGradient id="f1" cx="55%" cy="60%" r="65%"><stop offset="0" stop-color="#e4c8ae"/><stop offset=".45" stop-color="#7a8a4c"/><stop offset="1" stop-color="#3e4a26"/></radialGradient>
    <radialGradient id="f2" cx="45%" cy="60%" r="65%"><stop offset="0" stop-color="#f2ece4"/><stop offset=".45" stop-color="#9a8e80"/><stop offset="1" stop-color="#4a4638"/></radialGradient>
    <radialGradient id="f3" cx="50%" cy="55%" r="65%"><stop offset="0" stop-color="#f0ebe4"/><stop offset=".45" stop-color="#7c8a58"/><stop offset="1" stop-color="#34402a"/></radialGradient>
    <radialGradient id="f4" cx="50%" cy="60%" r="65%"><stop offset="0" stop-color="#ffffff"/><stop offset=".5" stop-color="#c8c8c0"/><stop offset="1" stop-color="#7a7c74"/></radialGradient>
  </defs>
  <rect width="1048" height="242" fill="#000"/>
  <rect x="0" y="10" width="1048" height="22" fill="url(#holes-b)"/>
  <rect x="0" y="210" width="1048" height="22" fill="url(#holes-b)"/>
  <rect x="6" y="38" width="252" height="168" fill="url(#f1)"/>
  <rect x="266" y="38" width="252" height="168" fill="url(#f2)"/>
  <rect x="528" y="38" width="252" height="168" fill="url(#f3)"/>
  <rect x="790" y="38" width="252" height="168" fill="url(#f4)"/>
</svg>

<div class="abs arrow-btn" style="left:544px;top:4332px">
  <svg width="14" height="14" viewBox="0 0 14 14" aria-hidden="true"><path d="M9 2 L4 7 L9 12" fill="none" stroke="#555" stroke-width="2"/></svg>
</div>
<div class="abs arrow-btn" style="left:608px;top:4332px">
  <svg width="14" height="14" viewBox="0 0 14 14" aria-hidden="true"><path d="M5 2 L10 7 L5 12" fill="none" stroke="#555" stroke-width="2"/></svg>
</div>
<div class="abs review-name" style="top:4412px">ELLIE + JAMES</div>
<div class="abs review-place" style="top:4445px">ASHCOMBE HALL, RUTLAND</div>

<!-- footer -->
<footer class="abs footer">
  <div class="abs brand-foot">
    <span style="display:block;width:30px;height:30px;border:2px solid #fff;margin:0 auto 10px"></span>
    <span style="display:block;font-size:20px;letter-spacing:6px">BMRT</span>
    <span style="display:block;font-size:10px;letter-spacing:5px;margin-top:4px">WEDDING FILMS</span>
  </div>
  <div class="abs" style="left:86px;top:152px;width:133px;height:136px;background:radial-gradient(ellipse 40% 35% at 50% 70%,#3a5aa0,rgba(58,90,160,0)),linear-gradient(180deg,#f2e8ee,#c8b8c4 45%,#8a7a6a)" role="img" aria-label="Wedding party group"></div>
  <div class="abs" style="left:227px;top:152px;width:133px;height:136px;background:radial-gradient(ellipse 25% 40% at 50% 55%,#2a2a2a,rgba(42,42,42,0)),linear-gradient(180deg,#d8d4c8,#7a8a5a 45%,#4a5036)" role="img" aria-label="Couple dancing outdoors"></div>
  <div class="abs" style="left:368px;top:152px;width:133px;height:136px;background:radial-gradient(ellipse 35% 30% at 50% 60%,#c87a8a,rgba(200,122,138,0)),linear-gradient(135deg,#e6d8cc,#a88a7a 60%,#6a5046)" role="img" aria-label="Bride with bouquet"></div>

  <div class="abs foot-col" style="left:585px;top:30px">
    <h4>LINKS</h4>
    <ul><li>HOME</li><li>FILMS</li><li>PRICES</li><li>REVIEWS</li><li>OPTIONS</li><li>ABOUT</li><li>CONTACT</li></ul>
  </div>
  <div class="abs foot-col" style="left:704px;top:30px">
    <h4>SITE MAP</h4>
    <ul><li>BLOG</li><li>PHOTOS</li><li>LOVE STORIES</li><li>RETRO VIDEO</li><li>MOMENTS</li><li>FAQS</li><li>CONTACT</li></ul>
  </div>
  <div class="abs foot-col" style="left:850px;top:30px">
    <h4>CONTACT</h4>
    <ul><li>07700 900 123</li><li>INFO@BMRTFILMS.COM</li></ul>
  </div>
</footer>
<div class="abs badge" role="img" aria-label="Featured listing badge"></div>
<div class="abs foot-rule"></div>
<div class="abs legal">BMRT FILMS LIMITED</div>
<span class="abs social" style="left:990px" aria-label="Social link"></span>
<span class="abs social" style="left:1028px" aria-label="Social link"></span>
<span class="abs social" style="left:1066px" aria-label="Social link"></span>

</body>
</html>
```